New Business Cards for NYC Salon

We are updating all of our cards. 7142-8863-2095 is my account number. We put names of our stylists on their cards. The back should include appointment space. Were looking for something more sleek and modern. Black/White Silver... or even touches of the orange color on our website which has been our thing for years. The design should communicate professional upscale boutique salon for men and women. Should be able to incorporate design into thank you cards, referral cards, brochure and postcards. The file is a zip file...we like the stacked ones black or white or the side versions.

Industry/Entity Type

Beauty Salon

Contact Information for Business Card

Marcus John's Salon313 W. 53rd Street, New York NY 10019 212-683-2741 info@marcusellingsalon.example www.marcusellingsalon.example

Font styles to use
Other font styles liked:
• trajan

Requirements
Must have
• we print a different card for every person in the salon. Begin by designing with the name Marcus. We will change it with every employee when printing. Must have a space for appointment date and time.
Nice to have
• Were looking to move towards the stacked or side placed logo but not opposed to utilizing the circular.
Should not have
• Photos

```html
<!DOCTYPE html>
<html lang="en">
<head>
<meta charset="utf-8">
<title>Marcus Elling's Salon – Business Card</title>
<link rel="stylesheet" href="https://fonts.googleapis.com/css2?family=Open+Sans:ital,wght@0,400;0,600;1,700&display=swap">
<style>
  :root {
    --stage: #161616;
    --card-white: #ffffff;
    --card-black: #050505;
    --ink: #111111;
    --paper-text: #f2f2f2;
    --rule: #8a8a8a;
    --edge: #2b2b2b;
  }
  * { margin: 0; padding: 0; box-sizing: border-box; }
  html, body { width: 1200px; height: 900px; overflow: hidden; }
  body {
    background: var(--stage);
    font-family: "Open Sans", Arial, sans-serif;
    position: relative;
  }
  .card {
    position: absolute;
    width: 429px;
    height: 249px;
    border-radius: 14px;
  }
  .card--front { left: 155px; top: 310px; background: var(--card-white); color: var(--ink); }
  .card--back { left: 631px; top: 312px; background: var(--card-black); color: var(--paper-text); border: 1px solid var(--edge); }

  .brand { position: absolute; left: 10px; top: 64px; width: 180px; text-align: center; }
  .brand__mark { display: block; margin: 0 auto 10px; }
  .brand__name { font-size: 11.5px; font-weight: 400; letter-spacing: 2.6px; line-height: 17px; text-transform: uppercase; }

  .contact { position: absolute; left: 192px; top: 52px; }
  .contact__title { font-size: 18.5px; font-weight: 600; line-height: 26px; margin-bottom: 15px; }
  .contact__address { font-size: 12.5px; line-height: 16px; margin-bottom: 16px; }
  .contact__list { list-style: none; font-size: 12.5px; line-height: 18px; }
  .contact__list li { display: flex; align-items: center; gap: 4px; }
  .contact__list svg { flex: none; }

  .appointment__title { position: absolute; left: 0; width: 100%; top: 34px; text-align: center; font-size: 18.5px; font-weight: 600; letter-spacing: -0.1px; }
  .appointment__row { position: absolute; left: 46px; font-size: 12px; display: flex; align-items: flex-end; }
  .appointment__row--name { top: 84px; }
  .appointment__row--date { top: 117px; }
  .appointment__row--time { top: 154px; }
  .appointment__line { display: inline-block; border-bottom: 1px solid var(--rule); height: 1px; margin-bottom: 4px; }
  .appointment__note { position: absolute; left: 0; width: 100%; padding-left: 18px; top: 197px; text-align: center; font-size: 11.5px; font-weight: 700; font-style: italic; }
  .appointment__mark { position: absolute; right: 34px; top: 42px; }
</style>
</head>
<body>
  <section class="card card--front" aria-label="Card front">
    <div class="brand">
      <svg class="brand__mark" width="20" height="20" viewBox="0 0 20 20" aria-hidden="true"><circle cx="10" cy="10" r="8" fill="var(--ink)"/></svg>
      <p class="brand__name">Marcus Elling's<br>Salon</p>
    </div>
    <div class="contact">
      <h1 class="contact__title">Marcus Elling's Salon</h1>
      <p class="contact__address">742 E. 18th Street,<br>New York NY 10003</p>
      <ul class="contact__list">
        <li><svg width="10" height="10" viewBox="0 0 10 10" aria-hidden="true"><path d="M1 3.5 Q5 0.5 9 3.5 L8 5 6.5 4 6.5 3 3.5 3 3.5 4 2 5Z M2.5 5.5 h5 l1 3.5 h-7Z" fill="var(--ink)"/></svg>212-683-2741</li>
        <li><svg width="10" height="10" viewBox="0 0 10 10" aria-hidden="true"><rect x="1" y="2.5" width="8" height="5.5" fill="var(--ink)"/><path d="M1 2.5 L5 5.5 L9 2.5" stroke="#fff" stroke-width="0.8" fill="none"/></svg>info@marcusellingsalon.example</li>
        <li><svg width="10" height="10" viewBox="0 0 10 10" aria-hidden="true"><path d="M4.5 5.5 L6.5 3.5 M3.5 4.5 L2 6 a1.4 1.4 0 0 0 2 2 L5.5 6.5 M6.5 5.5 L8 4 a1.4 1.4 0 0 0 -2 -2 L4.5 3.5" stroke="var(--ink)" stroke-width="1" fill="none" stroke-linecap="round"/></svg>marcusellingsalon.example</li>
      </ul>
    </div>
  </section>

  <section class="card card--back" aria-label="Card back">
    <h2 class="appointment__title">Your Next Appointment is</h2>
    <div class="appointment__row appointment__row--name">Name :&nbsp;&nbsp;&nbsp;&nbsp;<span class="appointment__line" style="width:262px"></span></div>
    <div class="appointment__row appointment__row--date">Date :&nbsp;&nbsp;&nbsp;<span class="appointment__line" style="width:268px"></span></div>
    <div class="appointment__row appointment__row--time">Time:&nbsp;&nbsp;&nbsp;<span class="appointment__line" style="width:93px"></span>&nbsp;&nbsp;AM&nbsp;&nbsp;&nbsp;&nbsp;&nbsp;&nbsp;<span class="appointment__line" style="width:121px"></span>&nbsp;&nbsp;&nbsp;PM</div>
    <p class="appointment__note">If unable to keep appointment, kindly give 24hrs notice.</p>
    <svg class="appointment__mark" width="14" height="14" viewBox="0 0 14 14" role="img" aria-label="Salon mark"><circle cx="7" cy="7" r="6" fill="var(--paper-text)"/></svg>
  </section>
</body>
</html>
```